Luxury Wine Label for New Startup Winery

We need a wine label for our new winery startup. We have worked with a local designer but do not feel the resulting label / logo have the elevation required to present our brand as a luxury wine. Our winery is called "Quailbrook Vineyards" and we are focused on extremely high quality hand crafted artisan and estate wines from the Pacific Northwest.
We would like to see designs that utilize a tree line, or other imagery that represents the "Quailbrook" part of our company name. Another interesting feature could be wood grain.
A logo will be required based on your design so please design with this in mind:
This logo should be consistent with the wine bottle label design, and should be representative of our high end exclusive wine while giving a sense of place (Oregon/ Pacific Northwest.)
I will supply an image of the design we received from our local designer, PLEASE NOTE: in general we do like wood grain and tree line concepts but feel the execution was poorly done.
ATTN: Logo design should be suitable for use on: Bottles (Red wine/rose/white wine), Bussiness cards, vehicle signage, business signage, etc
P.S.:
If you have a design that is not outside the box we are still interested in seeing it.
Label is for a burgundy style bottle with a label height of 3.5 - 4" and a width of 3.5-4"
any label <= 4"x4" and >=3.5"x3.5" will be acceptable:
HOWEVER Width should be greater than or equal to height due to the bottle format
Target Market(s)
Wine enthusiasts with adequate discretionary budgets to afford $100 bottles of wine.
Industry/Entity Type
Wine / Winery
Requirements
Must have
- A sense of luxury, a feel of exclusivity, and a theme consistent with our product and brand name
Nice to have
- Tree line, wood grain or other wood themes. Serif fonts
Should not have
- anything cheesy, off topic, hard to read script fonts or anything that makes the label hard to read from a few feet away or too busy

```html
<!DOCTYPE html>
<html lang="en">
<head>
<meta charset="utf-8">
<title>Quailbrook Vineyards — Syrah Label</title>
<link rel="stylesheet" href="https://fonts.googleapis.com/css2?family=Gilda+Display&family=Open+Sans:wght@400&display=swap">
<style>
  :root {
    --paper: #ffffff;
    --label-black: #0e0709;
    --dim-grey: #8a8a8a;
    --gold-light: #f3d97a;
    --gold-mid: #c9a23c;
    --gold-deep: #8a6418;
    --silver-light: #e6e6e6;
    --silver-mid: #b4b4b4;
    --silver-dark: #6f6f6f;
    --wood-dark: #2e1a0e;
    --wood-mid: #5a3418;
    --wood-light: #7a4a22;
    --stripe-dark: #3c3c3c;
    --box-ink: #2a1a08;
  }
  html, body {
    margin: 0;
    padding: 0;
    width: 1200px;
    height: 2402px;
    overflow: hidden;
    background: var(--paper);
  }
  .spec-sheet { display: block; width: 1200px; height: 2402px; }
  .dimension-label { font-family: "Open Sans", sans-serif; fill: var(--dim-grey); }
  .dimension-line { stroke: var(--dim-grey); stroke-width: 2; }
  .brand-name { font-family: "Gilda Display", serif; fill: url(#silver-text); }
  .region-name { font-family: "Gilda Display", serif; fill: url(#gold-text); letter-spacing: 4px; }
  .varietal-name { font-family: "Gilda Display", serif; fill: url(#silver-text); }
  .vintage-line { font-family: "Gilda Display", serif; fill: var(--box-ink); }
</style>
</head>
<body>
<svg class="spec-sheet" viewBox="0 0 1200 2402" xmlns="http://www.w3.org/2000/svg">
  <defs>
    <linearGradient id="silver-text" x1="0" y1="0" x2="1" y2="0">
      <stop offset="0" stop-color="#a9a9a9"/>
      <stop offset="0.45" stop-color="#e4e4e4"/>
      <stop offset="1" stop-color="#8c8c8c"/>
    </linearGradient>
    <linearGradient id="gold-text" x1="0" y1="0" x2="1" y2="0">
      <stop offset="0" stop-color="#d9b24a"/>
      <stop offset="0.5" stop-color="#b88a2a"/>
      <stop offset="1" stop-color="#f0d27a"/>
    </linearGradient>
    <linearGradient id="silver-band" x1="0" y1="0" x2="1" y2="0">
      <stop offset="0" stop-color="#9c9c9c"/>
      <stop offset="0.5" stop-color="#eeeeee"/>
      <stop offset="1" stop-color="#a6a6a6"/>
    </linearGradient>
    <linearGradient id="gold-band" x1="0" y1="0" x2="1" y2="0">
      <stop offset="0" stop-color="#a77b22"/>
      <stop offset="0.5" stop-color="#f3d97a"/>
      <stop offset="1" stop-color="#b88a2a"/>
    </linearGradient>
    <linearGradient id="treeline-tone" x1="0" y1="0" x2="1" y2="0">
      <stop offset="0" stop-color="#8a6418"/>
      <stop offset="0.5" stop-color="#d9b24a"/>
      <stop offset="1" stop-color="#f0d27a"/>
    </linearGradient>
    <linearGradient id="wood-tone" x1="0" y1="0" x2="0" y2="1">
      <stop offset="0" stop-color="#4a2a14"/>
      <stop offset="0.35" stop-color="#6a3c1c"/>
      <stop offset="0.7" stop-color="#3a2010"/>
      <stop offset="1" stop-color="#5a3418"/>
    </linearGradient>
    <pattern id="silver-stripes" width="10" height="7" patternUnits="userSpaceOnUse">
      <rect width="10" height="7" fill="url(#silver-band)"/>
      <rect y="5" width="10" height="2" fill="var(--stripe-dark)" opacity="0.55"/>
    </pattern>
  </defs>

  <!-- dimension marks: main label -->
  <g class="dimensions">
    <text class="dimension-label" x="253" y="85" font-size="40">4″</text>
    <line class="dimension-line" x1="170" y1="110" x2="1046" y2="110"/>
    <text class="dimension-label" x="20" y="236" font-size="40">3.25″</text>
    <line class="dimension-line" x1="139" y1="145" x2="139" y2="857"/>
    <line class="dimension-line" x1="1070" y1="145" x2="1070" y2="198"/>
    <text class="dimension-label" x="1100" y="190" font-size="40">1/4″</text>
    <line class="dimension-line" x1="1070" y1="803" x2="1070" y2="857"/>
    <text class="dimension-label" x="1100" y="848" font-size="40">1/4″</text>
    <line class="dimension-line" x1="378" y1="860" x2="378" y2="882"/>
    <text class="dimension-label" x="386" y="879" font-size="20">1/8″</text>

    <!-- dimension marks: varietal label -->
    <text class="dimension-label" x="20" y="997" font-size="40">7/8″</text>
    <line class="dimension-line" x1="139" y1="885" x2="139" y2="1077"/>
    <line class="dimension-line" x1="1070" y1="886" x2="1070" y2="908"/>
    <text class="dimension-label" x="1078" y="905" font-size="20">1/8″</text>
    <line class="dimension-line" x1="1070" y1="1052" x2="1070" y2="1074"/>
    <text class="dimension-label" x="1078" y="1071" font-size="20">1/8″</text>
    <line class="dimension-line" x1="170" y1="1093" x2="1046" y2="1093"/>
    <text class="dimension-label" x="253" y="1133" font-size="40">4″</text>
  </g>

  <!-- main label -->
  <g class="main-label">
    <rect x="170" y="145" width="876" height="53" fill="url(#silver-stripes)"/>
    <rect x="170" y="198" width="876" height="605" fill="var(--label-black)"/>
    <rect x="170" y="803" width="876" height="54" fill="url(#silver-stripes)"/>
    <rect class="treeline" x="400" y="245" width="418" height="131" rx="6" fill="url(#treeline-tone)" opacity="0.85"
          role="img" aria-label="Gold foil illustration of an evergreen tree line"/>
    <text class="brand-name" x="275" y="500" font-size="118" textLength="662" lengthAdjust="spacingAndGlyphs">QUAILBROOK</text>
    <text class="brand-name" x="290" y="608" font-size="118" textLength="640" lengthAdjust="spacingAndGlyphs">VINEYARDS</text>
    <text class="region-name" x="342" y="707" font-size="46" textLength="533" lengthAdjust="spacingAndGlyphs">WILLAMETTE  VALLEY</text>
  </g>

  <!-- varietal label -->
  <g class="varietal-label">
    <rect x="170" y="885" width="876" height="192" fill="url(#gold-band)"/>
    <g stroke="#5a3c0e" stroke-width="1.5" opacity="0.7">
      <line x1="170" y1="891" x2="1046" y2="891"/>
      <line x1="170" y1="897" x2="1046" y2="897"/>
      <line x1="170" y1="903" x2="1046" y2="903"/>
      <line x1="170" y1="1056" x2="1046" y2="1056"/>
      <line x1="170" y1="1062" x2="1046" y2="1062"/>
      <line x1="170" y1="1068" x2="1046" y2="1068"/>
      <line x1="170" y1="1074" x2="1046" y2="1074"/>
    </g>
    <rect class="wood-grain" x="170" y="910" width="876" height="140" fill="url(#wood-tone)"
          role="img" aria-label="Dark walnut wood grain planks"/>
    <text class="varietal-name" x="457" y="1006" font-size="92" textLength="298" lengthAdjust="spacingAndGlyphs">SYRAH</text>
    <rect x="476" y="1054" width="264" height="23" fill="url(#gold-band)"/>
    <text class="vintage-line" x="608" y="1073" font-size="20" text-anchor="middle">ESTATE | 2023 | GROWN</text>
  </g>
</svg>
</body>
</html>
```